Business Card Design - ChoiceCraft

Looking for creative, modern design, two sided for ChoiceCraft that is consistent with color and feel of website www.choicecraftpro.net.
Updates

Back of card will be used to promote products or have a quote revolving around decisions, change, leadership, innovation, creativity. Back should also have space to promote website, but optional to use the icon. Front of the card will need to use the icon and have standard place for name, job title, phone and email. We are not looking to put a mailing address or fax. Also want space to place a few words/phrase explaining what we do...such as individual growth and organizational development or tools, training, information...in addition, want the facebook icon small on the front somewhere as we are also on facebook.

Vector file uploaded of icon.

Target Market(s)

Professional coaching for individual growth and organizational development

Industry/Entity Type

Business

Requirements
Must have
• Icon...see attached.

```html
<!DOCTYPE html>
<html lang="en">
<head>
<meta charset="utf-8">
<title>ChoiceCraft Business Card</title>
<link rel="stylesheet" href="https://fonts.googleapis.com/css2?family=PT+Sans:wght@400;700&family=Jost:wght@400;500&family=Arimo:wght@400;700&display=swap">
<style>
  :root {
    --stage: #1d2026;
    --card: #ffffff;
    --ink: #222428;
    --ink-soft: #3c3f44;
    --blue-deep: #0b6fc0;
    --blue-mid: #1a8fd8;
    --blue-light: #38c3f0;
    --blue-pale: #bfe3f7;
    --grey-tab: #b9c0cc;
    --author: #1b8fd0;
  }
  * { box-sizing: border-box; margin: 0; padding: 0; }
  html, body { width: 1200px; height: 763px; overflow: hidden; }
  body {
    background: var(--stage);
    position: relative;
    font-family: "Jost", sans-serif;
  }
  .card {
    position: absolute;
    top: 231px;
    width: 525px;
    height: 300px;
    background: var(--card);
    border-radius: 18px;
    overflow: hidden;
  }
  .card--front { left: 50px; }
  .card--back { left: 625px; }

  /* Front */
  .brand {
    position: absolute;
    left: 140px; top: 44px;
    display: flex; align-items: center; gap: 16px;
  }
  .brand__dot {
    width: 64px; height: 64px; border-radius: 50%;
    background: var(--blue-mid);
  }
  .brand__name {
    font-family: "PT Sans", sans-serif;
    font-size: 30px; color: var(--ink);
  }
  .band-top {
    position: absolute; left: 235px; top: 150px;
    width: 252px; height: 26px;
    background: linear-gradient(90deg, var(--blue-mid), var(--blue-light));
  }
  .band-tab {
    position: absolute; left: 490px; top: 146px;
    width: 35px; height: 34px;
    background: linear-gradient(90deg, var(--grey-tab), #e4e8ee);
  }
  .band-name {
    position: absolute; left: 0; top: 176px;
    width: 380px; height: 30px;
    background: linear-gradient(90deg, var(--blue-deep), var(--blue-mid) 70%, var(--blue-light));
  }
  .band-name__text {
    position: absolute; left: 0; width: 380px; top: 177px;
    text-align: right; padding-right: 22px;
    font-family: "Arimo", sans-serif;
    color: #fff; font-size: 20px; font-weight: 700;
    line-height: 28px;
  }
  .band-name__text .title { font-weight: 400; font-size: 15px; }
  .contacts {
    position: absolute; left: 0; right: 0; top: 215px;
    text-align: center; color: var(--ink-soft);
    font-size: 14px; line-height: 22px;
  }
  .contacts .item { display: inline-flex; align-items: center; gap: 5px; margin: 0 8px; }
  .contacts svg { width: 12px; height: 12px; fill: var(--ink-soft); }
  .social-square { width: 10px; height: 10px; background: var(--blue-deep); display: inline-block; }
  .tagline {
    position: absolute; left: 0; right: 0; top: 264px;
    text-align: center; font-size: 14px; color: var(--ink-soft);
  }

  /* Back */
  .quotes {
    position: absolute; left: 30px; top: 26px; right: 20px;
    list-style: none;
    font-family: "Arimo", sans-serif;
  }
  .quote { margin-bottom: 9px; }
  .quote__text {
    font-size: 13px; color: var(--ink-soft); line-height: 17px;
  }
  .quote__text::before, .quote__text::after {
    font-family: "Arimo", sans-serif; font-weight: 700;
    font-size: 22px; color: var(--ink); line-height: 0;
    position: relative; top: 6px;
  }
  .quote__text::before { content: "\201C"; margin-right: 2px; }
  .quote__text::after { content: "\201D"; margin-left: 2px; top: 10px; }
  .quote__author {
    display: block; padding-left: 14px;
    font-size: 13px; font-weight: 700; color: var(--author);
  }
  .back-mark {
    position: absolute; right: 40px; bottom: 24px;
    display: flex; flex-direction: column; align-items: center; gap: 6px;
  }
  .back-mark__dot {
    width: 96px; height: 96px; border-radius: 50%;
    background: var(--blue-pale);
  }
  .back-mark__name {
    font-family: "PT Sans", sans-serif; font-size: 15px; color: var(--blue-mid);
  }
</style>
</head>
<body>
  <section class="card card--front" aria-label="Business card front">
    <div class="brand">
      <span class="brand__dot"></span>
      <span class="brand__name">ChoiceCraft</span>
    </div>
    <div class="band-top"></div>
    <div class="band-tab"></div>
    <div class="band-name"></div>
    <p class="band-name__text">Your Name, <span class="title">Title</span></p>
    <div class="contacts">
      <div>
        <span class="item"><svg viewBox="0 0 12 12"><path d="M3 1l2 2-1 1.5c.6 1.3 1.7 2.4 3 3L8.5 6.5l2 2-1.5 2C5 10 2 7 1.5 3z"/></svg>555-010-2468</span>
        <span class="item"><svg viewBox="0 0 12 12"><path d="M1 3h10v7H1z M1 3l5 4 5-4" fill="none" stroke="#3c3f44" stroke-width="1.2"/></svg>info@choicecraftmail.com</span>
      </div>
      <div>
        <span class="item"><svg viewBox="0 0 12 12"><circle cx="6" cy="6" r="5" fill="none" stroke="#3c3f44" stroke-width="1.2"/><path d="M1 6h10M6 1c-2 3-2 7 0 10M6 1c2 3 2 7 0 10" fill="none" stroke="#3c3f44" stroke-width="1"/></svg>www.choicecraftpro.net</span>
        <span class="item"><span class="social-square"></span>/choicecraftpro</span>
      </div>
    </div>
    <p class="tagline">Supporting individual growth &amp; organizational development.</p>
  </section>

  <section class="card card--back" aria-label="Business card back">
    <ul class="quotes">
      <li class="quote"><span class="quote__text">Try not to become a man of success, but rather a man of value.</span><span class="quote__author">- Alden Ross</span></li>
      <li class="quote"><span class="quote__text">The only constant is change.</span><span class="quote__author">- Helios Varn</span></li>
      <li class="quote"><span class="quote__text">We are what we repeatedly do. Excellence is not an act, it is a habit.</span><span class="quote__author">- Aris Tolman</span></li>
      <li class="quote"><span class="quote__text">Simplicity is the ultimate sophistication.</span><span class="quote__author">- Leon Davis</span></li>
      <li class="quote"><span class="quote__text">Life is not fair - get used to it.</span><span class="quote__author">- Will Yates</span></li>
    </ul>
    <div class="back-mark">
      <span class="back-mark__dot"></span>
      <span class="back-mark__name">ChoiceCraft</span>
    </div>
  </section>
</body>
</html>
```